Moravel Aesthetic Doctor

I require an elegant, luxurious looking business card for my aesthetic business. I am a doctor and that will set me aside from competitors. I am planning to provide home and spa based treatments to clients with high expectations. I have attached my logo.

```html
<!DOCTYPE html>
<html lang="en">
<head>
<meta charset="utf-8">
<title>Moravel Aesthetic Doctor – Business Card</title>
<link rel="stylesheet" href="https://fonts.googleapis.com/css2?family=Cormorant+Garamond:wght@400&family=Montserrat:wght@400;500&display=swap">
<style>
  :root {
    --backdrop: #3a3a3c;
    --card: #f7f7f7;
    --ink: #2f2f33;
    --muted: #8d8e91;
    --brand-blue: #2f9fe0;
    --ring: #a9aaad;
  }
  * { margin: 0; padding: 0; box-sizing: border-box; }
  html, body { width: 1200px; height: 900px; overflow: hidden; }
  body {
    background: var(--backdrop);
    font-family: "Montserrat", sans-serif;
    color: var(--ink);
    display: flex;
    justify-content: center;
    align-items: center;
    gap: 90px;
  }
  .card {
    width: 370px;
    height: 620px;
    background: var(--card);
    border-radius: 26px;
    box-shadow: 0 18px 40px rgba(0,0,0,.35);
    display: flex;
    flex-direction: column;
    align-items: center;
    text-align: center;
    padding: 70px 30px 40px;
  }
  .brand-mark {
    width: 120px; height: 120px;
    border: 3px solid var(--ring);
    border-radius: 50%;
    margin-bottom: 22px;
  }
  .brand-name {
    font-family: "Cormorant Garamond", serif;
    font-weight: 400;
    color: var(--muted);
    line-height: 1.05;
  }
  .brand-name .line-1 { display: block; font-size: 64px; letter-spacing: 3px; }
  .brand-name .line-2 { display: block; font-size: 27px; letter-spacing: 2px; text-transform: uppercase; }
  .tagline { margin-top: 14px; font-size: 15px; color: var(--ink); }
  .services {
    margin-top: auto;
    font-size: 14px;
    line-height: 1.55;
  }
  .accent-dash {
    width: 16px; height: 3px; background: var(--brand-blue);
    margin: 22px auto 0;
  }
  .doctor { margin-top: 40px; font-size: 15px; }
  .diploma { margin-top: 6px; font-size: 13px; color: var(--brand-blue); }
  .contact-icons { display: flex; gap: 22px; margin-top: 28px; }
  .contact-icons svg { width: 26px; height: 26px; }
  .contact-list { list-style: none; margin-top: 22px; font-size: 15px; line-height: 2.1; }
  .contact-list .highlight { color: var(--brand-blue); }
  .social { display: flex; gap: 10px; margin-top: 10px; }
  .social span {
    width: 20px; height: 20px; border-radius: 50%;
    background: var(--brand-blue);
  }
</style>
</head>
<body>

<section class="card card-front">
  <div class="brand-mark"></div>
  <h1 class="brand-name"><span class="line-1">MORAVEL</span><span class="line-2">Aesthetic Doctor</span></h1>
  <p class="tagline">Home and Spa Based Treatments</p>
  <p class="services">
    Dermal injectables | Plasma facials<br>
    Home and Spa Based Treatments<br>
    Microneedling | Skin boosters<br>
    Excessive sweating
  </p>
  <div class="accent-dash"></div>
</section>

<section class="card card-back">
  <div class="brand-mark"></div>
  <h2 class="brand-name"><span class="line-1">MORAVEL</span><span class="line-2">Aesthetic Doctor</span></h2>
  <p class="doctor">Dr. Elise Marwick MRCPCH MD</p>
  <p class="diploma">Australasian Diploma of Aesthetic Medicine</p>
  <div class="contact-icons">
    <svg viewBox="0 0 26 26" aria-label="Phone"><circle cx="13" cy="13" r="13" fill="#2f9fe0"/><path d="M8 9c0-1 1-2 2-2l1.5 2.5-1 1.2c.7 1.6 2 2.9 3.6 3.6l1.2-1L18 15c0 1-1 2-2 2-4.4 0-8-3.6-8-8z" fill="#fff"/></svg>
    <svg viewBox="0 0 26 26" aria-label="Email"><circle cx="13" cy="13" r="13" fill="#2f9fe0"/><rect x="7" y="9" width="12" height="8" fill="none" stroke="#fff" stroke-width="1.5"/><path d="M7 9l6 5 6-5" fill="none" stroke="#fff" stroke-width="1.5"/></svg>
    <svg viewBox="0 0 26 26" aria-label="Website"><circle cx="13" cy="13" r="13" fill="#2f9fe0"/><circle cx="13" cy="13" r="6" fill="none" stroke="#fff" stroke-width="1.5"/><path d="M7 13h12M13 7c-3 3-3 9 0 12M13 7c3 3 3 9 0 12" fill="none" stroke="#fff" stroke-width="1.2"/></svg>
  </div>
  <ul class="contact-list">
    <li>0800 555 019</li>
    <li>elise@moravel.co.nz</li>
    <li>www.<span class="highlight">moravel</span>.co.nz</li>
  </ul>
  <div class="social"><span></span><span></span></div>
</section>

</body>
</html>
```